Pepper & Palm Business Card FUN & EXCITING

Here is the Information for the Card:
Jaswinder Bains (Ravi)
E: RaviBains@postlark.com
C: (480) 555-0147
www.PepperPalmLV.com

We don't want traditional Indian cliche, We a playful bold and fun business card.

Files: https://files.cloudvessel.net/share/folders/7TqRmXpZ2vKa9LwBn4YcHd3JsEf6UoGi?usp=share_link

https://files.cloudvessel.net/share/folders/4MzXaQ8rTw2YbNcVk6PsLe5GhJdR3FoU?usp=share_link

Target Market(s)

Las Vegas Local Restaurant

Industry/Entity Type

Indian Restaurant

Contact Information for Business Card

Name, Email, Cell Phone, Company Logo

```html
<!DOCTYPE html>
<html lang="en">
<head>
<meta charset="utf-8">
<title>Pepper &amp; Palm – Business Card</title>
<link href="https://fonts.googleapis.com/css2?family=Montserrat:wght@400;600;800&display=swap" rel="stylesheet">
<style>
  :root {
    --backdrop: #2b2b2b;
    --card: #1c1c1c;
    --accent: #f07c22;
    --ink: #ffffff;
    --art-cream: #e9dfc6;
    --art-orange: #d9712b;
  }
  * { box-sizing: border-box; margin: 0; padding: 0; }
  html, body { width: 1200px; height: 1108px; overflow: hidden; }
  body {
    background: var(--backdrop);
    font-family: "Montserrat", sans-serif;
    color: var(--ink);
    position: relative;
  }
  .card {
    position: absolute;
    left: 258px;
    width: 700px;
    background: var(--card);
    border-radius: 18px;
    overflow: hidden;
  }
  .card::after {
    content: "";
    position: absolute;
    left: 0; right: 0; bottom: 0;
    height: 9px;
    background: var(--accent);
  }
  .card--front { top: 128px; height: 426px; }
  .card--back { top: 596px; height: 438px; }

  .brand {
    position: absolute;
    display: flex;
    flex-direction: column;
    align-items: center;
  }
  .brand__name {
    font-weight: 800;
    color: var(--ink);
    text-transform: uppercase;
    text-align: center;
    line-height: 0.95;
    letter-spacing: -0.01em;
  }
  .brand__art {
    border-radius: 16px;
    background: linear-gradient(160deg, var(--art-cream) 0%, var(--art-orange) 100%);
  }
  .card--front .brand { left: 0; right: 0; top: 92px; }
  .card--front .brand__name { font-size: 58px; }
  .card--front .brand__art { width: 220px; height: 136px; margin-top: 18px; }

  .card--back .brand { left: 130px; top: 186px; width: 130px; }
  .card--back .brand__name { font-size: 24px; }
  .card--back .brand__art { width: 96px; height: 60px; margin-top: 8px; border-radius: 8px; }

  .contact {
    position: absolute;
    left: 305px;
    top: 178px;
    padding-left: 12px;
    border-left: 2px solid var(--accent);
    height: 134px;
  }
  .contact__name {
    color: var(--accent);
    font-weight: 600;
    font-size: 27px;
    line-height: 1;
    margin-top: 4px;
    margin-bottom: 16px;
    white-space: nowrap;
  }
  .contact__list { list-style: none; }
  .contact__item {
    display: flex;
    align-items: center;
    font-size: 16.5px;
    font-weight: 400;
    height: 29px;
    white-space: nowrap;
  }
  .contact__icon {
    width: 14px; height: 14px;
    margin-right: 22px;
    fill: var(--accent);
    flex: none;
  }
</style>
</head>
<body>
  <section class="card card--front">
    <div class="brand">
      <p class="brand__name">Pepper<br>&amp; Palm</p>
      <div class="brand__art" role="img" aria-label="Area for the brand mascot artwork"></div>
    </div>
  </section>

  <section class="card card--back">
    <div class="brand">
      <p class="brand__name">Pepper<br>&amp; Palm</p>
      <div class="brand__art" role="img" aria-label="Area for the brand mascot artwork"></div>
    </div>
    <div class="contact">
      <h1 class="contact__name">Jaswinder Bains (Ravi)</h1>
      <ul class="contact__list">
        <li class="contact__item">
          <svg class="contact__icon" viewBox="0 0 16 16" aria-hidden="true"><path d="M1 5c0-2 3-3 7-3s7 1 7 3v1h-4V5H5v1H1z M3 7h10l1 6H2z M8 8.5a2 2 0 1 0 0 4a2 2 0 0 0 0-4z"/></svg>
          (480) 555-0147
        </li>
        <li class="contact__item">
          <svg class="contact__icon" viewBox="0 0 16 16" aria-hidden="true"><path d="M1 3h14v1.5L8 9 1 4.5z M1 6.3 8 10.8l7-4.5V13H1z"/></svg>
          RaviBains@postlark.com
        </li>
        <li class="contact__item">
          <svg class="contact__icon" viewBox="0 0 16 16" aria-hidden="true"><path d="M8 1a7 7 0 1 0 0 14A7 7 0 0 0 8 1zm-1 2.2c-.5 1-1.8 1.3-2 2.5-.2 1 1 1.5 1.8 1.3.9-.2 1.4.8 1.1 1.7-.3 1 .2 2 .9 2.8.2.3-.1.8-.5.8A5 5 0 0 1 7 3.2zm3.5.7a5 5 0 0 1 2 6.5c-.4-.6-1.2-.7-1.7-1.2-.6-.6-.2-1.6-.8-2.2-.5-.5-1.5-.4-1.7-1.1-.2-.8 1-1.4 2.2-2z"/></svg>
          www.PepperPalmLV.com
        </li>
      </ul>
    </div>
  </section>
</body>
</html>
```